Electrictrian Contractor Website Design

We are working with an electrical contractor in California called Fennick Electric.

Some sites to use for content/competitors and inspiration:
https://corvanelectric.example
https://tralvenpage.example/web/contractor/ (lots of contractor website designs we've approved and continue to show clients)

Thank you for taking the time to consider designing a website for us. We are web developers based in Stockton, CA, USA. Most of our projects go through the same process. Understanding this process may help you win a project with us. We custom-code all of our websites in-house. We don’t have any requirements as to what tools you use for your design, but we prefer Figma files. For any design that we label as four-stars, we send it to the client for review. The client picks the final design they want us to use. Once we complete this process, we will continue to show additional clients all the four-star sites and purchase them later. Your designs will have multiple chances to sell. For better chances of success, we ask that you follow these guidelines.

IMAGES:
If you use any images or icons in the design, we ask that you have a link to the asset so we can purchase the image/icon. Most of the designs we submit do not have the customer’s images on them unless they have some great images. Be creative; show us the feeling you are trying to portray with your image choices. Use any royalty-free site you choose. We subscribe to Quorvane and mainly use their images, but we can purchase images outside of Quorvane.

PLEASE NOTE: we will not submit designs to clients with watermarks on the images.

FONTS:
We ask that you identify the fonts used in the design. This can be done in a message if you want. We typically use Pellmarsh Type and Quorvane Type.

CONTENT:
We're always open to different content and ideas. We often submit designs with stock images so the client can see our vision. We typically take pictures after the website launch to use their images with our vision. Lorem Ipsum is fine for paragraphs, but we ask that you write the headers in correct English. We want to be able to show the vision and identify the sections of the website.

INSPIRATION:
We typically add a couple of links in the brief of websites we like to help you get started in your design.

REVISIONS:
We do not often ask for revisions of the designs unless we see something in the design that may not appeal to the client. If there are slight changes that we want to make, we do that in the development process.

FEEDBACK:
We rarely give feedback on designs during the design process. We are working on many website projects and do not have the time to provide feedback. We usually respond if your request is well thought out and asks specific questions, but a note asking “feedback, please” usually goes unanswered

```html
<!DOCTYPE html>
<html lang="en">
<head>
<meta charset="utf-8">
<title>Fennick Electric</title>
<link rel="stylesheet" href="https://fonts.googleapis.com/css2?family=Montserrat:wght@400;500;600;700;800&family=Roboto:wght@400;500;700&family=Yellowtail&display=swap">
<style>
:root{
  --blue:#0b4390;
  --blue-dark:#083a7d;
  --yellow:#f7b500;
  --ink:#1d1d1f;
  --muted:#6b6b72;
  --pale:#edf3fb;
  --white:#ffffff;
}
*{box-sizing:border-box;margin:0;padding:0}
html,body{width:1200px;height:3813px;overflow:hidden}
body{position:relative;font-family:'Roboto',sans-serif;color:var(--ink);background:var(--white)}
.abs{position:absolute}

/* header */
.site-header{position:absolute;left:0;top:0;width:1200px;height:105px;background:var(--white);z-index:5}
.brand{position:absolute;left:110px;top:20px;display:flex;flex-direction:column;align-items:center;color:var(--blue);font-family:'Montserrat',sans-serif;font-weight:500;line-height:1;white-space:nowrap}
.brand .b1{font-size:27px;letter-spacing:9px;padding-left:9px}
.brand .b2{font-size:27px;letter-spacing:4px;padding-left:4px;margin-top:6px}
.socials{position:absolute;left:567px;top:19px;display:flex;gap:11px}
.socials span{width:28px;height:28px;border:1px solid #c9c9cf;border-radius:50%;display:block}
.quote-btn{position:absolute;left:755px;top:14px;width:136px;height:37px;background:var(--yellow);color:var(--white);font:700 13px 'Roboto',sans-serif;display:flex;align-items:center;justify-content:center;gap:6px;border-radius:2px}
.main-nav{position:absolute;left:330px;top:65px;width:622px;height:40px;background:var(--blue);clip-path:polygon(22px 0,100% 0,100% 100%,0 100%);display:flex;align-items:center;padding-left:10px}
.main-nav a{color:var(--white);font:500 15px 'Roboto',sans-serif;text-decoration:none;height:40px;display:flex;align-items:center;padding:0 25px;border-right:1px solid rgba(255,255,255,.18)}
.main-nav a.active{background:var(--yellow);padding:0 32px;border:none}
.call-box{position:absolute;left:935px;top:0;width:265px;height:105px;background:var(--yellow);clip-path:polygon(30px 0,100% 0,100% 100%,0 100%);color:var(--white)}
.call-box .ic{position:absolute;left:42px;top:32px;width:42px;height:42px;border-radius:50%;background:var(--blue);display:flex;align-items:center;justify-content:center}
.call-box small{position:absolute;left:100px;top:32px;font:500 12px 'Roboto',sans-serif}
.call-box strong{position:absolute;left:100px;top:52px;font:700 21px 'Roboto',sans-serif;letter-spacing:.5px}

/* hero */
.hero-edge{position:absolute;left:0;top:105px;width:1200px;height:715px;background:var(--blue);clip-path:polygon(0 0,100% 0,100% 520px,600px 713px,0 553px)}
.hero-photo{position:absolute;left:0;top:105px;width:1200px;height:715px;clip-path:polygon(0 0,100% 0,100% 510px,600px 700px,0 545px);background:linear-gradient(100deg,#2b2117 0%,#463522 35%,#7a5e2c 60%,#b99233 80%,#6f5a33 100%)}
.hero-photo::after{content:"";position:absolute;inset:0;background:linear-gradient(90deg,rgba(20,16,12,.55),rgba(20,16,12,0) 70%)}
.hero-copy{position:absolute;left:110px;top:262px;width:600px;color:var(--white);z-index:2}
.hero-copy h1{font:700 48px/1.22 'Montserrat',sans-serif;letter-spacing:.5px}
.hero-copy h1 span{font-weight:400;display:block}
.hero-copy p{font:500 16px/1.65 'Roboto',sans-serif;margin-top:24px;width:570px}
.btn{display:inline-flex;align-items:center;justify-content:center;background:var(--yellow);color:var(--white);font:700 14px 'Roboto',sans-serif;border-radius:2px;text-transform:uppercase}
.hero-copy .btn{margin-top:30px;width:222px;height:46px}

/* about */
.about-art .shape{position:absolute}
.eyebrow{color:var(--yellow);font:500 16px 'Roboto',sans-serif}
.about-text{position:absolute;left:627px;top:864px;width:470px}
.about-text h2{font:700 33px/1.15 'Montserrat',sans-serif;color:var(--blue);margin-top:13px;white-space:nowrap}
.about-text h2 span{font-weight:400;display:block}
.about-text p{font:400 14px/1.7 'Roboto',sans-serif;color:var(--muted);text-align:justify;margin-top:22px;width:425px}
.about-text p+p{margin-top:14px}
.about-text .btn{margin-top:32px;width:162px;height:45px}

/* sections */
.section-title{position:absolute;left:0;width:1200px;text-align:center}
.section-title .eyebrow{display:block}
.section-title h2{font:400 34px 'Montserrat',sans-serif;color:var(--blue);margin-top:8px}
.section-title h2 b{font-weight:700}
.services-band{position:absolute;left:0;top:1357px;width:1200px;height:662px;background:var(--pale)}
.card{position:absolute;width:308px;background:var(--white);box-shadow:0 4px 14px rgba(10,40,90,.12);text-align:center}
.card .photo{height:231px;border:3px solid var(--white);border-bottom:none}
.service-card{top:1517px;height:391px}
.service-card .badge{position:absolute;left:120px;top:166px;width:68px;height:68px;border-radius:50%;display:flex;align-items:center;justify-content:center;border:3px solid var(--white)}
.card h3{font:500 19px 'Roboto',sans-serif;color:var(--ink)}
.service-card h3{margin-top:26px}
.card p{font:400 14px/1.7 'Roboto',sans-serif;color:var(--muted);margin:12px auto 0;width:270px}
.more{display:inline-flex;align-items:center;gap:6px;color:var(--yellow);font:700 13px 'Roboto',sans-serif;margin-top:18px}

/* testimonials */
.testi{position:absolute;left:0;top:2019px;width:1200px;height:447px;background:var(--blue);overflow:hidden}
.testi .yellow{position:absolute;inset:0;background:var(--yellow);clip-path:polygon(0 0,405px 0,165px 100%,0 100%)}
.testi-head{position:absolute;left:110px;top:78px;color:var(--white)}
.testi-head .eyebrow{color:var(--white);font-weight:700;font-size:18px}
.testi-head h2{font:400 35px/1.2 'Montserrat',sans-serif;margin-top:10px}
.testi-head h2 b{font-weight:700;display:block}
.testi-photo{position:absolute;left:98px;top:226px;width:174px;height:174px;border-radius:50%;background:radial-gradient(circle at 40% 40%,#f3c035,#b78a1e 45%,#3c4f7a 100%)}
.review{position:absolute;top:101px;width:314px;height:223px;background:var(--white);padding:22px 22px}
.review p{font:400 14px/1.75 'Roboto',sans-serif;color:var(--muted)}
.reviewer{position:absolute;left:22px;bottom:18px;display:flex;align-items:center;gap:10px}
.avatar{width:50px;height:50px;border-radius:50%;background:linear-gradient(#c9ccd3,#6d7280)}
.reviewer strong{display:block;font:500 15px 'Roboto',sans-serif}
.stars{color:var(--yellow);font-size:12px;letter-spacing:2px}
.qmark{position:absolute;right:18px;bottom:6px;color:var(--yellow);font:700 80px/1 'Montserrat',sans-serif;height:50px}

/* news */
.news-card{top:2641px;height:374px}
.news-card .photo{height:204px;border:none}
.date{position:absolute;left:40px;top:186px;width:228px;height:32px;background:var(--blue);color:var(--white);font:400 14px/32px 'Roboto',sans-serif}
.news-card h3{margin-top:42px;font-size:17px}
.news-card p{margin-top:10px;font-size:13.5px}
.news-card .more{margin-top:14px}

/* cta */
.cta{position:absolute;left:0;top:3127px;width:1200px;height:296px;background:linear-gradient(90deg,#f2b80c,#eab21a 40%,#e3ad22 60%,#f0b610)}
.cta h2{position:absolute;left:0;top:60px;width:1200px;text-align:center;color:var(--white);font:700 32px/1.15 'Montserrat',sans-serif}
.cta h2 span{display:block;font-weight:400}
.cta .phone-ic{position:absolute;left:272px;top:174px;width:42px;height:42px;border-radius:50%;background:var(--white);display:flex;align-items:center;justify-content:center}
.cta .need{position:absolute;left:328px;top:167px;color:var(--white);font:500 17px 'Roboto',sans-serif}
.cta .number{position:absolute;left:328px;top:188px;color:var(--white);font:400 32px 'Roboto',sans-serif;white-space:nowrap}
.cta .number b{font-weight:700}
.cta .or{position:absolute;left:668px;top:170px;color:var(--white);font:400 36px 'Yellowtail',cursive}
.cta .btn-blue{position:absolute;left:751px;top:171px;width:204px;height:47px;background:var(--blue);color:var(--white);font:700 15px 'Roboto',sans-serif;display:flex;align-items:center;justify-content:center;gap:7px;border-radius:2px}

/* footer */
.site-footer{position:absolute;left:0;top:3423px;width:1200px;height:390px;background:var(--blue);color:var(--white)}
.site-footer .brand{left:110px;top:125px;color:var(--white)}
.site-footer .brand .b1,.site-footer .brand .b2{font-size:34px}
.site-footer .brand .b1{letter-spacing:11px;padding-left:11px}
.site-footer .brand .b2{letter-spacing:5px;padding-left:5px;margin-top:8px}
.fcol{position:absolute;top:88px}
.fcol h4{font:700 16px 'Roboto',sans-serif;margin-bottom:20px}
.fcol li{list-style:none;font:400 13.5px 'Roboto',sans-serif;margin-bottom:10px}
.contact-item{position:relative;padding-left:22px;margin-bottom:14px;font:400 13.5px/1.45 'Roboto',sans-serif}
.contact-item strong{display:block;font-size:12px;font-weight:700}
.contact-item svg{position:absolute;left:0;top:2px}
.to-top{position:absolute;left:1132px;top:248px;width:36px;height:36px;border-radius:50%;background:var(--yellow);display:flex;align-items:center;justify-content:center}
.divider{position:absolute;left:110px;top:312px;width:980px;height:1px;background:rgba(255,255,255,.25)}
.copyright{position:absolute;left:0;top:347px;width:1200px;text-align:center;font:400 14px 'Roboto',sans-serif}
</style>
</head>
<body>

<header class="site-header">
  <div class="brand"><span class="b1">FENNICK</span><span class="b2">ELECTRIC</span></div>
  <div class="socials" aria-label="Social links"><span></span><span></span><span></span><span></span></div>
  <div class="quote-btn">GET A QUOTE
    <svg width="13" height="13" viewBox="0 0 14 14"><circle cx="7" cy="7" r="7" fill="#fff"/><path d="M5.5 4 8.5 7 5.5 10" stroke="#f7b500" stroke-width="2" fill="none"/></svg>
  </div>
  <nav class="main-nav">
    <a class="active">Home</a><a>About Us</a><a>Services</a><a>Our Projects</a><a style="border:none">Contact Us</a>
  </nav>
  <div class="call-box">
    <div class="ic"><svg width="22" height="22" viewBox="0 0 24 24"><path d="M6.6 10.8a15 15 0 0 0 6.6 6.6l2.2-2.2a1 1 0 0 1 1-.25 11 11 0 0 0 3.6.6 1 1 0 0 1 1 1V20a1 1 0 0 1-1 1A17 17 0 0 1 3 4a1 1 0 0 1 1-1h3.5a1 1 0 0 1 1 1c0 1.25.2 2.45.6 3.6a1 1 0 0 1-.25 1z" fill="#fff"/></svg></div>
    <small>Call Us Today</small>
    <strong>555-014-2290</strong>
  </div>
</header>

<section class="hero">
  <div class="hero-edge"></div>
  <div class="hero-photo" role="img" aria-label="Photo of two electricians in hard hats testing an electrical panel"></div>
  <div class="hero-copy">
    <h1>RELIABILITY, QUALITY <span>AND EXPERTISE</span></h1>
    <p>Lorem ipsum dolor sit amet, consectetur adipiscing elit, sed do eiusmod tempor incididunt ut labore et dolore magna aliqua.</p>
    <span class="btn">Request an Appointment</span>
  </div>
</section>

<section class="about">
  <div class="about-art">
    <div class="shape" style="left:0;top:905px;width:40px;height:70px;background:var(--yellow);clip-path:polygon(0 0,100% 50%,0 100%)"></div>
    <div class="shape" role="img" aria-label="Photo of an electrician using a tablet beside a switchboard" style="left:78px;top:875px;width:437px;height:375px;background:linear-gradient(120deg,#5d6670,#9aa3a8 40%,#c7d83a 65%,#3d4650);clip-path:polygon(50% 0,100% 100%,0 100%)"></div>
    <div class="shape" role="img" aria-label="Photo of a smiling electrician in an orange hard hat" style="left:342px;top:929px;width:227px;height:196px;background:linear-gradient(100deg,#9aa0a6,#d7d9db 50%,#e9a23a 80%,#f2b24a);clip-path:polygon(0 0,100% 0,43% 100%,25% 45%)"></div>
    <div class="shape" style="left:41px;top:1127px;width:96px;height:83px;background:var(--blue);clip-path:polygon(0 0,100% 0,50% 100%)"></div>
  </div>
  <div class="about-text">
    <span class="eyebrow">About Us</span>
    <h2>AS AN INDUSTRY EXPERT, <span>FENNICK ELECTRIC</span></h2>
    <p>Lorem ipsum dolor sit amet, consectetur adipiscing elit, sed do eiusmod tempor incididunt ut labore et dolore magna aliqua. Ut ulnisi ut aliquip ex ea commodo consequat.</p>
    <p>Duis aute irure dolor in reprehenderit in voluptate velit esse cillum dolore eu fugiat nulla pariatur. Excepteur sint occaecat cupidatat non proident, sunt in culpa qui officia deserunt mollit anim id omnis iste natus error sit voluptatem est laborum.</p>
    <span class="btn">Learn More</span>
  </div>
</section>

<section class="services">
  <div class="services-band"></div>
  <div class="section-title" style="top:1408px"><span class="eyebrow">What We Do</span><h2><b>OUR</b> SERVICES</h2></div>

  <article class="card service-card" style="left:112px">
    <div class="photo" role="img" aria-label="Photo of wind turbines beside a battery storage facility" style="background:linear-gradient(180deg,#7f9bb8,#c7cdd2 50%,#6f7f62 80%,#4f6a3a)"></div>
    <div class="badge" style="background:var(--blue)"><svg width="30" height="30" viewBox="0 0 30 30" fill="none" stroke="#fff" stroke-width="1.6"><rect x="5" y="12" width="20" height="14"/><path d="M3 12 15 5l12 7"/><rect x="12" y="18" width="6" height="8"/></svg></div>
    <h3>Industrial &amp; Agriculture</h3>
    <p>Lorem ipsum dolor sit amet, consectetur adipiscing elit, sed do eiusmod</p>
    <span class="more">READ MORE <svg width="12" height="12" viewBox="0 0 14 14"><circle cx="7" cy="7" r="7" fill="#f7b500"/><path d="M5.5 4 8.5 7 5.5 10" stroke="#fff" stroke-width="2" fill="none"/></svg></span>
  </article>

  <article class="card service-card" style="left:446px">
    <div class="photo" role="img" aria-label="Photo of a worker in an orange hard hat inside a lit tunnel" style="background:linear-gradient(120deg,#1e5c7a,#5fa9c4 40%,#e07a2a 75%,#2a4a63)"></div>
    <div class="badge" style="background:var(--yellow)"><svg width="30" height="30" viewBox="0 0 30 30" fill="none" stroke="#fff" stroke-width="1.6"><path d="M4 26h22M8 26V10h5v16M17 26V6h5v20M8 14h5M17 12h5"/></svg></div>
    <h3>Underground and Civil work</h3>
    <p>Lorem ipsum dolor sit amet, consectetur adipiscing elit, sed do eiusmod</p>
    <span class="more">READ MORE <svg width="12" height="12" viewBox="0 0 14 14"><circle cx="7" cy="7" r="7" fill="#f7b500"/><path d="M5.5 4 8.5 7 5.5 10" stroke="#fff" stroke-width="2" fill="none"/></svg></span>
  </article>

  <article class="card service-card" style="left:779px">
    <div class="photo" role="img" aria-label="Photo of an electrician testing wiring in a residential panel" style="background:linear-gradient(100deg,#d9a93a,#8c8f94 35%,#c6c9cc 65%,#7d8288)"></div>
    <div class="badge" style="background:var(--blue)"><svg width="30" height="30" viewBox="0 0 30 30" fill="none" stroke="#fff" stroke-width="1.6"><rect x="7" y="5" width="10" height="21"/><rect x="17" y="12" width="7" height="14"/><path d="M10 9h4M10 13h4M10 17h4M20 16h1M20 20h1"/></svg></div>
    <h3>Multifamily / Residential</h3>
    <p>Lorem ipsum dolor sit amet, consectetur adipiscing elit, sed do eiusmod</p>
    <span class="more">READ MORE <svg width="12" height="12" viewBox="0 0 14 14"><circle cx="7" cy="7" r="7" fill="#f7b500"/><path d="M5.5 4 8.5 7 5.5 10" stroke="#fff" stroke-width="2" fill="none"/></svg></span>
  </article>
</section>

<section class="testi">
  <div class="yellow"></div>
  <div class="testi-head">
    <span class="eyebrow">Testimonials</span>
    <h2>WHAT OUR <b>CUSTOMER SAYS</b></h2>
  </div>
  <div class="testi-photo" role="img" aria-label="Round photo of gloved hands working on electrical wiring"></div>

  <div class="review" style="left:461px">
    <p>Lorem ipsum dolor sit amet, consectetur adipiscing elit, sed do eiusmod tempor incididunt ut labore et dolore magna minim veniam, quis aliqua.</p>
    <div class="reviewer"><div class="avatar" role="img" aria-label="Customer portrait"></div><div><strong>Marla T. Venn</strong><span class="stars">★★★★★</span></div></div>
    <span class="qmark">“</span>
  </div>
  <div class="review" style="left:804px">
    <p>Lorem ipsum dolor sit amet, consectetur adipiscing elit, sed do eiusmod tempor incididunt ut labore et dolore magna minim veniam, quis aliqua.</p>
    <div class="reviewer"><div class="avatar" role="img" aria-label="Customer portrait"></div><div><strong>Marla T. Venn</strong><span class="stars">★★★★★</span></div></div>
    <span class="qmark">“</span>
  </div>
</section>

<section class="news">
  <div class="section-title" style="top:2526px"><span class="eyebrow">Latest Update</span><h2><b>LAEST</b> NEWS</h2></div>

  <article class="card news-card" style="left:111px">
    <div class="photo" role="img" aria-label="Photo of two engineers at an electrical substation" style="background:linear-gradient(180deg,#c9ced3,#8e959b 55%,#5a5f52)"></div>
    <div class="date">September 10, 2024 &nbsp;|&nbsp; Orin Pell</div>
    <h3>Lorem ipsum dolor sit amet,</h3>
    <p>Sed ut perspiciatis unde omnis iste natus error sit voluptatem accusantium</p>
    <span class="more">READ MORE <svg width="12" height="12" viewBox="0 0 14 14"><circle cx="7" cy="7" r="7" fill="#f7b500"/><path d="M5.5 4 8.5 7 5.5 10" stroke="#fff" stroke-width="2" fill="none"/></svg></span>
  </article>
  <article class="card news-card" style="left:446px">
    <div class="photo" role="img" aria-label="Photo of hands wiring circuit breakers" style="background:linear-gradient(120deg,#6e5538,#c8b796 45%,#e2dccd 70%,#8a7b5c)"></div>
    <div class="date">September 10, 2024 &nbsp;|&nbsp; Orin Pell</div>
    <h3>Lorem ipsum dolor sit amet,</h3>
    <p>Sed ut perspiciatis unde omnis iste natus error sit voluptatem accusantium</p>
    <span class="more">READ MORE <svg width="12" height="12" viewBox="0 0 14 14"><circle cx="7" cy="7" r="7" fill="#f7b500"/><path d="M5.5 4 8.5 7 5.5 10" stroke="#fff" stroke-width="2" fill="none"/></svg></span>
  </article>
  <article class="card news-card" style="left:780px">
    <div class="photo" role="img" aria-label="Photo of an electrician in a white hard hat working on a control panel" style="background:linear-gradient(100deg,#e6e8ea,#9aa39a 40%,#3e5f6b 70%,#26323a)"></div>
    <div class="date">September 10, 2024 &nbsp;|&nbsp; Orin Pell</div>
    <h3>Lorem ipsum dolor sit amet,</h3>
    <p>Sed ut perspiciatis unde omnis iste natus error sit voluptatem accusantium</p>
    <span class="more">READ MORE <svg width="12" height="12" viewBox="0 0 14 14"><circle cx="7" cy="7" r="7" fill="#f7b500"/><path d="M5.5 4 8.5 7 5.5 10" stroke="#fff" stroke-width="2" fill="none"/></svg></span>
  </article>
</section>

<section class="cta" role="img" aria-label="Yellow-tinted photo of electricians at work behind the call to action">
  <h2>DAY OR NIGH, 24/7, COUNT ON TRUSTED <span>SERCICE FROM FENNICK ELECTRIC</span></h2>
  <div class="phone-ic"><svg width="22" height="22" viewBox="0 0 24 24"><path d="M6.6 10.8a15 15 0 0 0 6.6 6.6l2.2-2.2a1 1 0 0 1 1-.25 11 11 0 0 0 3.6.6 1 1 0 0 1 1 1V20a1 1 0 0 1-1 1A17 17 0 0 1 3 4a1 1 0 0 1 1-1h3.5a1 1 0 0 1 1 1c0 1.25.2 2.45.6 3.6a1 1 0 0 1-.25 1z" fill="#f7b500"/></svg></div>
  <span class="need">Need help now?</span>
  <span class="number">Call: <b>555-018-3344</b></span>
  <svg class="abs" style="left:628px;top:150px" width="100" height="30" viewBox="0 0 100 30" fill="none" stroke="#fff" stroke-width="1.5"><path d="M2 26C25 6 60 2 96 10"/><path d="M88 4l8 6-9 4"/></svg>
  <span class="or">or</span>
  <span class="btn-blue">SCHEDULE SERVICE <svg width="13" height="13" viewBox="0 0 14 14"><circle cx="7" cy="7" r="7" fill="#fff"/><path d="M5.5 4 8.5 7 5.5 10" stroke="#0b4390" stroke-width="2" fill="none"/></svg></span>
</section>

<footer class="site-footer">
  <div class="brand"><span class="b1">FENNICK</span><span class="b2">ELECTRIC</span></div>
  <div class="fcol" style="left:434px"><h4>Quick Links</h4><ul><li>Home</li><li>About Us</li><li>Services</li><li>Testimonial</li><li>Contact Us</li></ul></div>
  <div class="fcol" style="left:646px"><h4>About Company</h4><ul><li>Terms of Use</li><li>Terms &amp; Condition</li><li>News</li><li>Privacy Policy</li><li>FAQ</li></ul></div>
  <div class="fcol" style="left:870px;width:230px"><h4>Contact Us</h4>
    <div class="contact-item"><svg width="12" height="14" viewBox="0 0 12 16"><path d="M6 0a6 6 0 0 0-6 6c0 4.5 6 10 6 10s6-5.5 6-10a6 6 0 0 0-6-6zm0 8.5A2.5 2.5 0 1 1 6 3.5a2.5 2.5 0 0 1 0 5z" fill="#f7b500"/></svg><strong>Location</strong>2418 Lorem ipsum dolor amet, consectetur adipiscing elit</div>
    <div class="contact-item"><svg width="13" height="13" viewBox="0 0 24 24"><path d="M6.6 10.8a15 15 0 0 0 6.6 6.6l2.2-2.2a1 1 0 0 1 1-.25 11 11 0 0 0 3.6.6 1 1 0 0 1 1 1V20a1 1 0 0 1-1 1A17 17 0 0 1 3 4a1 1 0 0 1 1-1h3.5a1 1 0 0 1 1 1c0 1.25.2 2.45.6 3.6a1 1 0 0 1-.25 1z" fill="#f7b500"/></svg><strong>Phone</strong>(555) 018 – 3344</div>
    <div class="contact-item"><svg width="14" height="11" viewBox="0 0 14 11"><rect width="14" height="11" rx="1" fill="#f7b500"/><path d="M0 1l7 5 7-5" stroke="#0b4390" stroke-width="1.3" fill="none"/></svg><strong>Email</strong>info@fennickelectric.example</div>
  </div>
  <div class="to-top"><svg width="14" height="14" viewBox="0 0 14 14"><path d="M3 9l4-4 4 4" stroke="#fff" stroke-width="2" fill="none"/></svg></div>
  <div class="divider"></div>
  <p class="copyright">2024 Copyright - Fennick Electric &nbsp;|&nbsp;All Rights Reserved</p>
</footer>

</body>
</html>
```